Medical Practice needs a Letterhead Design

We need a clean, modern letterhead design for our stem cell medical practice.

Industry/Entity Type

Medical

```html
<!DOCTYPE html>
<html lang="en">
<head>
<meta charset="UTF-8">
<title>Aurelle Medical Letterhead</title>
<link rel="stylesheet" href="https://fonts.googleapis.com/css2?family=Arimo:wght@400;700&display=swap">
<style>
  :root {
    --backdrop: #e9e8e4;
    --paper: #ffffff;
    --ink-navy: #1f3446;
    --ink-text: #1d2b3a;
    --accent-green: #b6c84a;
    --mark-grey: #c4c4c9;
    --mark-green: #ecefd6;
  }
  * { margin: 0; padding: 0; box-sizing: border-box; }
  html, body {
    width: 1200px;
    height: 800px;
    overflow: hidden;
    background: var(--backdrop);
    font-family: "Arimo", Arial, sans-serif;
  }
  .canvas {
    position: relative;
    width: 1200px;
    height: 800px;
  }
  .letterhead {
    position: absolute;
    left: 331px;
    top: 20px;
    width: 537px;
    height: 760px;
    background: var(--paper);
    box-shadow: 0 6px 18px rgba(0, 0, 0, 0.18);
  }
  .brand-watermark {
    position: absolute;
    left: 96px;
    top: 148px;
    width: 366px;
    height: 350px;
    border-radius: 50%;
    background: radial-gradient(circle at 60% 50%, var(--mark-green) 0%, rgba(236, 239, 214, 0.35) 55%, rgba(255, 255, 255, 0) 72%);
  }
  .brand-name {
    position: absolute;
    left: 31px;
    top: 690px;
    display: flex;
    align-items: center;
    gap: 6px;
    font-size: 17px;
    font-weight: 700;
    color: var(--ink-navy);
    white-space: nowrap;
  }
  .brand-dot {
    width: 9px;
    height: 9px;
    border-radius: 50%;
    background: var(--ink-navy);
  }
  .divider {
    position: absolute;
    left: 205px;
    top: 666px;
    width: 1px;
    height: 64px;
    background: var(--accent-green);
  }
  .contact {
    position: absolute;
    left: 225px;
    top: 690px;
    font-size: 8.5px;
    line-height: 10.5px;
    color: var(--ink-text);
    white-space: nowrap;
  }
</style>
</head>
<body>
  <main class="canvas">
    <section class="letterhead">
      <div class="brand-watermark" role="img" aria-label="Faint brand symbol decoration"></div>
      <div class="brand-name"><span class="brand-dot"></span>Aurelle Medical</div>
      <div class="divider"></div>
      <address class="contact">
        <div>Address line 1</div>
        <div>Tel:00 00 0000 0000 Fax : 00000000 Mobile :00 00000 00000</div>
        <div>Email: abc@def.com Website:www.abcdef.com</div>
      </address>
    </section>
  </main>
</body>
</html>
```